Brightmoor Essentials colloidal silver spray for pets.

We need a label for an 8-oz cobalt blue spray bottle. We are a small company just starting to share the benefits of colloidal silver. Our first offering will be the 8-oz spray bottle for pets. We would also like to update our logo. The finished project should be crisp and incorporate a dog on the label. I have attached the information we would like on the label and our logo, which can be changed to match your vision.
Updates

Hi, I would like to remind you that we are using a cobalt blue bottle with a black sprayer and would like an updated logo. Also, for the business cards, we don't want an animal on them, as we are planning future products for people. thank you

```html
<!DOCTYPE html>
<html lang="en">
<head>
<meta charset="utf-8">
<title>Brightmoor Essentials – Colloidal Silver Pet Spray Label</title>
<link rel="stylesheet" href="https://fonts.googleapis.com/css2?family=Abril+Fatface&family=Lexend:wght@400;600;800&family=PT+Serif:ital@1&display=swap">
<style>
  :root {
    --canvas-bg: #f1f1f1;
    --label-white: #f3f3f5;
    --leaf-green: #6fb52c;
    --leaf-green-deep: #5aa51f;
    --title-green-light: #8fcb45;
    --title-green: #5fa51e;
    --ink-navy: #1f1d5e;
    --dog-gold-light: #e9c37e;
    --dog-gold: #c98d3e;
    --dog-gold-deep: #9a6426;
    --white: #ffffff;
  }
  * { box-sizing: border-box; margin: 0; padding: 0; }
  html, body { width: 1200px; height: 1126px; overflow: hidden; }
  body { background: var(--canvas-bg); position: relative; }

  .label {
    position: absolute;
    left: 200px; top: 128px;
    width: 800px; height: 870px;
    overflow: hidden;
    background: var(--leaf-green);
  }
  .label-shapes { position: absolute; inset: 0; width: 800px; height: 870px; }

  .brand {
    position: absolute;
    left: 0; width: 800px; top: 58px;
    text-align: center;
    font-family: "Lexend", sans-serif;
    font-weight: 800;
    color: var(--ink-navy);
    line-height: 1;
    letter-spacing: 1px;
  }
  .brand-name { display: block; font-size: 44px; }
  .brand-sub { display: block; font-size: 30px; margin-top: 6px; letter-spacing: 3px; }

  .product-title {
    position: absolute;
    left: 0; width: 800px; top: 185px;
    text-align: center;
    font-family: "Abril Fatface", serif;
    font-weight: 400;
    font-size: 112px;
    line-height: 0.96;
    color: var(--title-green);
    background: linear-gradient(90deg, var(--title-green-light), var(--title-green));
    -webkit-background-clip: text;
    background-clip: text;
    -webkit-text-fill-color: transparent;
  }
  .product-title span { display: block; }

  .dog-portrait {
    position: absolute;
    left: 92px; top: 415px;
    width: 292px; height: 455px;
    border-radius: 140px 140px 20px 20px;
    background: radial-gradient(ellipse at 50% 35%, var(--dog-gold-light), var(--dog-gold) 60%, var(--dog-gold-deep));
  }

  .claims {
    position: absolute;
    left: 412px; top: 466px;
    list-style: none;
    font-family: "Lexend", sans-serif;
    font-weight: 400;
    font-size: 32px;
    color: var(--ink-navy);
  }
  .claims li {
    display: flex; align-items: center;
    height: 58px;
  }
  .claims svg { width: 30px; height: 26px; margin-right: 20px; flex: none; }

  .tagline {
    position: absolute;
    left: 407px; top: 642px;
    width: 324px; height: 46px;
    border: 2.5px solid var(--ink-navy);
    border-radius: 23px;
    font-family: "PT Serif", serif;
    font-style: italic;
    font-size: 26px;
    color: var(--ink-navy);
    display: flex; align-items: center; justify-content: center;
  }

  .net-weight {
    position: absolute;
    left: 402px; top: 790px;
    font-family: "Lexend", sans-serif;
    font-weight: 800;
    font-size: 28px;
    color: var(--white);
    letter-spacing: -0.5px;
  }
</style>
</head>
<body>
  <section class="label">
    <svg class="label-shapes" viewBox="0 0 800 870" aria-hidden="true">
      <path fill="var(--label-white)"
        d="M0 0 L620 0 C730 40 790 140 800 255 L800 722 C640 700 470 700 360 725
           C250 660 160 600 105 520 C45 430 10 300 0 180 Z"/>
    </svg>

    <div class="brand">
      <span class="brand-name">BRIGHTMOOR</span>
      <span class="brand-sub">ESSENTIALS</span>
    </div>

    <h1 class="product-title"><span>Colloidal</span><span>Silver</span></h1>

    <div class="dog-portrait" role="img" aria-label="Photograph of a smiling golden retriever"></div>

    <ul class="claims">
      <li><svg viewBox="0 0 30 26"><path fill="var(--leaf-green-deep)" d="M2 2 C18 2 28 10 28 24 C14 24 4 16 2 2 Z"/></svg>100% Pure</li>
      <li><svg viewBox="0 0 30 26"><path fill="var(--leaf-green-deep)" d="M2 2 C18 2 28 10 28 24 C14 24 4 16 2 2 Z"/></svg>No Preservatives</li>
      <li><svg viewBox="0 0 30 26"><path fill="var(--leaf-green-deep)" d="M2 2 C18 2 28 10 28 24 C14 24 4 16 2 2 Z"/></svg>No Additives</li>
    </ul>

    <p class="tagline">Natural First Aid for Pets</p>

    <p class="net-weight">Net Weight: 250ml | 8oz</p>
  </section>
</body>
</html>
```